K & R Acre Works. Business card design

We need a business card designed for a new business. We have a bulldozer and tractor service. We clear land and make wildlife food plots. We provide disking, bush hogging, and site prep services.
I have attached an image of a business card that I like and would like my business cards to look similar.

Target Market(s)

anyone needing bulldozer and/or tractor services

Industry/Entity Type

Business

Contact Information for Business Card

K & R Acre Works, Operated by 7-T-Ranch
Wade Colton
601-472-3358
wcr4817@fieldmail-example.com

Font styles to use
Sans Serif

Colors

Designer to choose colors to be used in the design.

Requirements
Must have
• image of tractor and bulldozer
• Land Clearing
• Wildlife food plots
• Bush Hogging
• Disking
• Site prep
Nice to have
• i have included a image of a business card that i like. I would like mine to be similar.

```html
<!DOCTYPE html>
<html lang="en">
<head>
<meta charset="utf-8">
<title>K &amp; R Acre Works – Business Card</title>
<link href="https://fonts.googleapis.com/css2?family=Roboto:wght@400;500;700&family=Roboto+Condensed:wght@400;700&display=swap" rel="stylesheet">
<style>
  :root {
    --page-bg: #e8e6e1;
    --card-white: #f7f7f6;
    --olive: #9a9633;
    --olive-text: #8d8a2a;
    --brown-dark: #6a4419;
    --brown-orange: #c47a2c;
    --text-dark: #3a2a14;
    --white: #ffffff;
  }
  html, body {
    margin: 0;
    width: 1200px;
    height: 771px;
    overflow: hidden;
    background: var(--page-bg);
  }
  .business-card {
    position: absolute;
    left: 90px;
    top: 93px;
    width: 1020px;
    height: 585px;
    filter: drop-shadow(0 6px 14px rgba(0,0,0,0.25));
  }
  .card-text { font-family: "Roboto", Arial, sans-serif; }
  .brand-name { font-family: "Roboto Condensed", "Roboto", Arial, sans-serif; font-weight: 700; font-size: 21px; fill: var(--brown-dark); letter-spacing: 0.3px; }
  .brand-tagline { font-family: "Roboto Condensed", "Roboto", Arial, sans-serif; font-weight: 400; font-size: 12.5px; fill: var(--text-dark); }
  .brand-operator { font-family: "Roboto Condensed", "Roboto", Arial, sans-serif; font-weight: 400; font-size: 11px; fill: var(--text-dark); }
  .person-name { font-weight: 700; font-size: 22px; fill: var(--olive-text); }
  .person-title { font-weight: 500; font-size: 13px; fill: var(--brown-dark); }
  .contact-line { font-weight: 400; font-size: 13px; fill: var(--white); }
  .services-heading { font-weight: 700; font-size: 15.5px; fill: var(--white); }
  .service-item { font-weight: 400; font-size: 13.5px; fill: var(--white); }
</style>
</head>
<body>
<svg class="business-card" viewBox="0 0 600 344" xmlns="http://www.w3.org/2000/svg">
  <defs>
    <clipPath id="card-shape"><rect width="600" height="344" rx="18"/></clipPath>
    <linearGradient id="machinery-tone" x1="0" y1="0" x2="1" y2="0.3">
      <stop offset="0" stop-color="#8e8e8e"/>
      <stop offset="0.55" stop-color="#b9b9b9"/>
      <stop offset="1" stop-color="#f7f7f6" stop-opacity="0"/>
    </linearGradient>
    <linearGradient id="tractor-tone" x1="0" y1="0" x2="0" y2="1">
      <stop offset="0" stop-color="#5d7a3c"/>
      <stop offset="0.5" stop-color="#d9462a"/>
      <stop offset="1" stop-color="#6f6a4a"/>
    </linearGradient>
  </defs>

  <g clip-path="url(#card-shape)">
    <rect class="card-base" width="600" height="344" fill="var(--card-white)"/>

    <rect class="bulldozer-photo" x="0" y="0" width="360" height="300" fill="url(#machinery-tone)"
          role="img" aria-label="Black and white photo of a bulldozer clearing land"/>

    <path class="wave-band-dark" fill="var(--brown-dark)"
          d="M0,224 C40,250 65,292 112,292 C200,292 290,150 420,108 C490,86 545,78 600,100 L600,344 L0,344 Z"/>
    <path class="wave-band-orange" fill="var(--brown-orange)"
          d="M0,232 C40,258 65,299 112,299 C200,299 290,160 420,118 C490,96 545,90 600,112 L600,344 L0,344 Z"/>
    <path class="wave-olive" fill="var(--olive)"
          d="M0,242 C40,266 65,306 112,306 C200,306 290,170 420,129 C490,107 545,102 600,125 L600,344 L0,344 Z"/>
  </g>

  <circle class="tractor-photo-frame" cx="89" cy="188" r="72" fill="var(--white)"/>
  <circle class="tractor-photo" cx="89" cy="188" r="67" fill="url(#tractor-tone)"
          role="img" aria-label="Photo of a red tractor with front loader"/>

  <g class="card-text">
    <rect class="brand-mark" x="37" y="51" width="16" height="16" fill="var(--brown-dark)"/>
    <text class="brand-name" x="59" y="67">K &amp; R ACRE WORKS</text>
    <text class="brand-tagline" x="37" y="82">FOR ALL OF YOUR LAND IMPROVEMENT NEEDS</text>
    <text class="brand-operator" x="37" y="96">Operated by 7-T-Ranch</text>

    <text class="person-name" x="564" y="49" text-anchor="end">WADE COLTON</text>
    <text class="person-title" x="564" y="65" text-anchor="end">OWNER</text>

    <g class="contact-list">
      <text class="contact-line" x="538" y="153" text-anchor="end">601-472-3358</text>
      <path class="icon-phone" fill="var(--white)" d="M545,144 l3,-1 l2,3 l-1.6,1.4 q1,2.4 3.3,3.4 l1.4,-1.6 l3,2 l-1,3 q-5,0 -8.3,-3.3 q-3,-3 -2.8,-6.9 z"/>
      <text class="contact-line" x="538" y="171" text-anchor="end">wcr4817@fieldmail-example.com</text>
      <g class="icon-mail">
        <rect x="544" y="162" width="13" height="9" rx="1" fill="var(--white)"/>
        <path d="M544.5,162.5 L550.5,167.5 L556.5,162.5" fill="none" stroke="var(--olive)" stroke-width="1.2"/>
      </g>
      <text class="contact-line" x="538" y="189" text-anchor="end">kracreworks.example</text>
      <g class="icon-web">
        <circle cx="550.5" cy="184.5" r="6" fill="var(--white)"/>
        <g fill="none" stroke="var(--olive)" stroke-width="1">
          <ellipse cx="550.5" cy="184.5" rx="2.6" ry="5.4"/>
          <line x1="545" y1="184.5" x2="556" y2="184.5"/>
        </g>
      </g>
    </g>

    <text class="services-heading" x="556" y="218" text-anchor="end">WE PROVIDE</text>
    <g class="service-list">
      <text class="service-item" x="545" y="237" text-anchor="end">Land Clearing</text>
      <text class="service-item" x="545" y="255" text-anchor="end">Wildlife food plots</text>
      <text class="service-item" x="545" y="273" text-anchor="end">Bush Hogging</text>
      <text class="service-item" x="545" y="291" text-anchor="end">Disking</text>
      <text class="service-item" x="545" y="309" text-anchor="end">Site prep</text>
      <g class="service-bullets" fill="var(--white)">
        <circle cx="553" cy="232.5" r="2"/>
        <circle cx="553" cy="250.5" r="2"/>
        <circle cx="553" cy="268.5" r="2"/>
        <circle cx="553" cy="286.5" r="2"/>
        <circle cx="553" cy="304.5" r="2"/>
      </g>
    </g>
  </g>
</svg>
</body>
</html>
```